Business Name: DM Space Arranging Pty Ltd

Business Type: Professional Home Styling and Minor Renovation Business

Logo: Attached is the logo that has been created.
I always envisaged the logo in the middle of the business card with my full name underneath it.

Marnie Tulloch B.Com LMR HTV
Property Stylist & Project Manager

Include dot points of services
Staging Houses for Sale
Minor Home Renovations
Home Styling & Project Management
Re-Designing Living Spaces to Aid the Disabled

Somewhere on the card I would like to incorporate
"Property Styling and Cosmetic Renovations"

Colour Scheme:
Gloss black business card, with white and then
Gold or Silver as the highlight colours.

Incorporate a small amount of yellow only if possible to make it pop. If this really doesn’t work it doesn’t have to be used. Also l like the colour teal if that needs to be used as a contrast colour.

Feel/Themes
• I love antique chairs, regal expensive looking furniture mixed with modern homes (this is the unique style I want to sell) antique and modern mix that looks high class as well as modern and fresh, targeting an executive market.
• I want to use an orchid as a trademark throughout the course of my work, not sure if this can somehow be incorporated? Also really like crowns to give that regal/antique feel and then something else to give that modern twist (I don’t know what the something else could be)
• Wall Paper Look (on a portion of it not all of it, like a French look)
• Overall feel - A very deluxe and professional feel with a little bit of creative flare.

I hope this helps create a bit of a picture.

Is it ok that I call you tomorrow morning? My mobile number is 0438 926 574 if you have any questions for me in the meantime.

Target Market(s)

High Quality Executive Market - People selling homes

Industry/Entity Type

Business

Contact Information for Business Card

Include dot points of services:
Staging Houses for Sale
Minor Home Renovations

Font styles to use
Serif
Script

Colors
33b8a4
fbed22

Requirements
Must have
• Marnie Tulloch B.Com LMR HTV
• Property Stylist & Project Manager
• LMR and HTV Logos on the card
• "Dramatically increase the value of your property"
Nice to have
• Colour Scheme:
• Gloss black business card, with white and then
• Gold or Silver as the highlight colours.
• Incorporate a small amount of yellow only if possible to make it pop. If this really doesn’t work it doesn’t have to be used. Also l like the colour teal if that needs to be used as a contrast colour.
• Also like teal as a highlight colour.

```html
<!DOCTYPE html>
<html lang="en">
<head>
<meta charset="utf-8">
<title>DM Space Arranging Pty Ltd – Business Card</title>
<link rel="stylesheet" href="https://fonts.googleapis.com/css2?family=EB+Garamond:wght@400;500&family=Great+Vibes&display=swap">
<style>
  :root {
    --backdrop: #26272a;
    --card-white: #ffffff;
    --gloss-black: #0b0b0c;
    --gloss-sheen: #2a2a2c;
    --gold: #c9962b;
    --gold-light: #f1cf6a;
    --silver: #9a9a9a;
    --ink: #1d1d1d;
    --teal: #33b8a4;
  }
  * { box-sizing: border-box; margin: 0; padding: 0; }
  html, body { width: 1200px; height: 852px; overflow: hidden; }
  body {
    background: var(--backdrop);
    font-family: "EB Garamond", Georgia, serif;
    position: relative;
  }
  .card {
    position: absolute;
    width: 520px;
    height: 300px;
    border-radius: 10px;
    overflow: hidden;
    background: var(--card-white);
    box-shadow: 0 14px 30px rgba(0,0,0,.45);
  }
  .card--front { left: 80px; top: 110px; }
  .card--back  { left: 600px; top: 442px; }

  /* shared business name block */
  .business-name {
    display: flex;
    align-items: center;
    gap: 10px;
  }
  .business-name__mark {
    width: 14px; height: 14px;
    border-radius: 50%;
    background: var(--silver);
    flex: none;
  }
  .business-name__text {
    font-size: 15px;
    letter-spacing: 3px;
    text-transform: uppercase;
    color: var(--ink);
    padding: 5px 0;
    border-top: 1px solid var(--ink);
    border-bottom: 1px solid var(--ink);
    white-space: nowrap;
  }

  /* front */
  .card--front .business-name {
    position: absolute;
    left: 0; right: 0; top: 72px;
    justify-content: center;
  }
  .gloss-band {
    position: absolute;
    left: 0; right: 0; bottom: 0;
    height: 128px;
    background: linear-gradient(160deg, var(--gloss-black) 0%, var(--gloss-sheen) 45%, var(--gloss-black) 70%);
    padding: 20px 0 0 150px;
  }
  .holder-name {
    font-family: "Great Vibes", cursive;
    font-size: 36px;
    line-height: 1;
    color: var(--gold);
  }
  .holder-credentials, .holder-role {
    font-size: 15px;
    color: var(--silver);
    line-height: 1.3;
  }
  .holder-credentials { padding-left: 30px; margin-top: 4px; }
  .holder-role { padding-left: 12px; }

  /* back */
  .card--back .business-name {
    position: absolute;
    left: 56px; top: 62px;
  }
  .services {
    position: absolute;
    left: 40px; top: 160px;
    list-style: none;
    font-size: 16px;
    color: var(--ink);
    line-height: 1.4;
  }
  .services li::before {
    content: "»";
    color: var(--teal);
    margin-right: 10px;
  }
  .tagline-strip {
    position: absolute;
    top: 0; right: 0; bottom: 0;
    width: 58px;
    background: var(--gloss-black);
    border-left: 4px solid var(--gold);
    display: flex;
    align-items: center;
    justify-content: center;
  }
  .tagline-strip__text {
    writing-mode: vertical-rl;
    font-size: 15px;
    letter-spacing: .5px;
    color: var(--gold-light);
    white-space: nowrap;
  }
</style>
</head>
<body>
  <section class="card card--front" aria-label="Business card front">
    <div class="business-name">
      <span class="business-name__mark"></span>
      <span class="business-name__text">DM Space Arranging Pty Ltd</span>
    </div>
    <div class="gloss-band">
      <p class="holder-name">Marnie Tulloch</p>
      <p class="holder-credentials">B.Com LMR HTV</p>
      <p class="holder-role">Property Stylist &amp; Project Manager</p>
    </div>
  </section>

  <section class="card card--back" aria-label="Business card back">
    <div class="business-name">
      <span class="business-name__mark"></span>
      <span class="business-name__text">DM Space Arranging Pty Ltd</span>
    </div>
    <ul class="services">
      <li>Staging Houses for Sale</li>
      <li>Minor Home Renovations</li>
      <li>Home Styling &amp; Project Management</li>
      <li>Re-Designing Living Spaces to Aid the Disabled</li>
    </ul>
    <div class="tagline-strip">
      <span class="tagline-strip__text">Property Styling &amp; Cosmetic Renovations</span>
    </div>
  </section>
</body>
</html>
```